Brand Identity Stationary Package

Hello I'm looking for a full branding package for my Property Management Company. I have a logo but looking to have the following
Business Card
Email signature
Facebook cover photo
Letterhead (word.doc)
#10 Envelope
Pocket Folder - link to 9x12 pocket folder design specs https://www.printorbit-example.ca/marketing-materials/presentation-folders
would like everything to match and be brand identifiable. The company looks after residential properties/apartments and some commercial properties. Attached is a zip of the files.
For Business Card
Name: Gareth Lindqvist
Position: Operations Manager
Number: 1 (555) 384-2917
Email: Gareth@harborkey-example.ca
Website: Harborkey-example.ca
Property Management

```html
<!DOCTYPE html>
<html lang="en">
<head>
<meta charset="utf-8">
<title>Harborkey Property Management – Stationery</title>
<link href="https://fonts.googleapis.com/css2?family=Questrial&family=Roboto:wght@300;400&display=swap" rel="stylesheet">
<style>
  :root{
    --backdrop:#a9aaad;
    --paper:#ffffff;
    --brand-green:#80a83f;
    --ink:#231f20;
    --body-text:#3d3d3d;
    --muted:#555555;
    --sig-tone:#e4e4e4;
  }
  *{box-sizing:border-box;margin:0;padding:0}
  html,body{width:1200px;height:857px;overflow:hidden;background:var(--backdrop)}
  body{position:relative;font-family:"Questrial",sans-serif;color:var(--ink)}
  .piece{position:absolute;background:var(--paper);overflow:hidden}
  .abs{position:absolute}
  .wordmark{font-family:"Questrial",sans-serif;font-weight:400;line-height:1;white-space:nowrap;color:var(--ink)}
  .tagline{font-family:"Questrial",sans-serif;line-height:1;white-space:nowrap;color:var(--ink)}
  .on-green .wordmark,.on-green .tagline{color:#fff}
  .contact{font-family:"Questrial",sans-serif;color:var(--ink);white-space:nowrap;display:flex;align-items:center;gap:2px}
  .contact svg{fill:none;stroke:var(--brand-green);flex:none}
  .contact svg.solid{fill:var(--brand-green);stroke:none}
  .web{font-family:"Questrial",sans-serif;color:var(--brand-green);white-space:nowrap;text-align:right}
  .dash{position:absolute;height:2px;background:var(--brand-green)}
  .bottom-band{position:absolute;left:0;right:0;bottom:0;background:var(--brand-green)}

  /* Letterhead */
  .letterhead{left:274px;top:146px;width:400px;height:566px}
  .letterhead .wordmark{left:37px;top:33px;font-size:21px;letter-spacing:1.2px}
  .letterhead .tagline{left:38px;top:53px;font-size:4.6px;letter-spacing:3.6px}
  .letter-body{position:absolute;left:43px;width:315px;font-family:"Roboto",sans-serif;font-weight:300;font-size:6.3px;line-height:9.45px;color:var(--body-text)}
  .letter-body p{text-align:justify}
  .signature{position:absolute;left:43px;top:438px;width:92px;height:14px;background:var(--sig-tone);border-radius:2px}
  .letterhead .contact{font-size:6.6px;left:35px}
  .letterhead .web{font-size:6.6px;right:36px;top:535px}

  /* Business card front */
  .card-front{left:62px;top:472px;width:187px;height:107px}
  .card-front .wordmark{left:17px;top:17px;font-size:11px;letter-spacing:.7px}
  .card-front .tagline{left:17px;top:29px;font-size:2.4px;letter-spacing:1.9px}
  .card-front .person{left:17px;top:59px;font-size:5.6px;color:var(--brand-green);font-weight:700}
  .card-front .role{left:17px;top:66px;font-size:4px;color:var(--muted)}
  .card-front .contact{font-size:4px;left:17px}
  .card-front .web{font-size:4px;right:18px;top:90px}

  /* Business card back */
  .card-back{left:62px;top:605px;width:187px;height:107px;background:var(--brand-green)}
  .card-back .wordmark{left:0;right:0;text-align:center;top:45px;font-size:15px;letter-spacing:1.2px}
  .card-back .tagline{left:0;right:0;text-align:center;top:62px;font-size:3.5px;letter-spacing:3px}
  .card-back .web-light{left:0;right:0;text-align:center;top:89px;font-size:4px;letter-spacing:1px;color:#fff}

  /* Email signature */
  .email-sig{left:699px;top:186px;width:302px;height:92px}
  .email-sig .brand-panel{position:absolute;left:0;top:0;width:110px;height:100%;background:var(--brand-green)}
  .email-sig .wordmark{left:13px;top:38px;font-size:11.5px;letter-spacing:.8px}
  .email-sig .tagline{left:13px;top:51px;font-size:2.6px;letter-spacing:2px}
  .email-sig .person{left:128px;top:21px;font-size:8.6px;color:var(--brand-green);font-weight:700}
  .email-sig .role{left:128px;top:31px;font-size:6.4px;color:var(--muted)}
  .email-sig .social{position:absolute;left:235px;top:26px;display:flex;gap:3.3px}
  .email-sig .social span{width:9.5px;height:9.5px;border-radius:50%;background:var(--brand-green)}
  .email-sig .contact{font-size:5.6px;left:128px}
  .email-sig .web{font-size:5.6px;right:19px;top:63px}

  /* Envelope front */
  .envelope-front{left:699px;top:303px;width:440px;height:191px}
  .envelope-front .wordmark{left:39px;top:33px;font-size:19px;letter-spacing:1.2px}
  .envelope-front .tagline{left:39px;top:52px;font-size:4.6px;letter-spacing:3.5px}
  .envelope-front .contact{font-size:6.6px;left:39px}
  .envelope-front .web{font-size:6.6px;right:39px;top:163px}

  /* Envelope back */
  .envelope-back{left:699px;top:520px;width:440px;height:192px;background:transparent}
  .envelope-back svg.shape{position:absolute;inset:0}
  .envelope-back .wordmark{left:0;right:0;text-align:center;top:20px;font-size:17px;letter-spacing:1.6px}
  .envelope-back .tagline{left:0;right:0;text-align:center;top:37px;font-size:4px;letter-spacing:3.6px}
</style>
</head>
<body>

<!-- Letterhead -->
<section class="piece letterhead" aria-label="Letterhead">
  <div class="abs wordmark">HARBORKEY</div>
  <div class="abs tagline">PROPERTY MANAGEMENT</div>

  <div class="letter-body" style="top:138px">01 January 2050</div>
  <div class="letter-body" style="top:157px">Company (Pvt) Ltd.<br>PO Box 3355 Mainville St<br>Sample City Country 3355</div>
  <div class="letter-body" style="top:203px">Dear Colin Ashworth,</div>
  <div class="letter-body" style="top:222px"><p>Lorem ipsum dolor sit amet, consectetuer adipiscing elit, sed diam nonummy nibh euismod tincidunt ut laoreet dolore magna aliquam erat volutpat. Ut wisi enim ad minim veniam, quis nostrud exerci tation ullamcorper suscipit lobortis nisl ut aliquip ex ea commodo consequat. Duis dolore te feugait nulla facilisi. Nam liber tempor cum soluta nobis eleifend option congue nihil imperdiet doming id quod mazim placerat facer possim assum. Lorem ipsum dolor sit amet, consectetuer adipiscing elit, sed diam nonummy nibh euismod tincidunt ut laoreet dolore magna aliquam erat volutpat. Ut wisi enim ad minim veniam, quis nostrud exerci tation ullamcorper suscipit lobortis nisl ut aliquip ex ea commodo consequat.</p></div>
  <div class="letter-body" style="top:298px"><p>Consectetuer adipiscing elit, sed diam nonummy nibh euismod tincidunt ut laoreet dolore magna aliquam erat volutpat. Ut wisi enim ad minim veniam, quis nostrud exerci tation ullamcorper suscipit lobortis nisl ut aliquip ex ea commodo consequat. Consectetuer adipiscing elit, sed diam nonummy nibh euismod tincidunt ut laoreet dolore magna aliquam erat volutpat. Ut wisi enim ad minim veniam, quis nostrud exerci tation ullamcorper suscipit lobortis nisl ut aliquip ex ea commodo consequat.</p></div>
  <div class="letter-body" style="top:354px"><p>Consectetuer adipiscing elit, sed diam nonummy nibh euismod tincidunt ut laoreet dolore magna aliquam erat volutpat. Ut wisi enim ad minim veniam, quis nostrud exerci tation ullamcorper suscipit lobortis nisl ut aliquip ex ea commodo consequat. Consectetuer adipiscing elit, sed diam nonummy nibh euismod tincidunt ut laoreet dolore magna aliquam erat volutpat. Ut wisi enim ad minim veniam, quis nostrud exerci tation ullamcorper suscipit lobortis nisl ut aliquip ex ea commodo consequat.</p></div>
  <div class="letter-body" style="top:425px">Sincerely Yours</div>
  <div class="signature" role="img" aria-label="Handwritten signature of Desmond Halloway"></div>

  <div class="abs contact" style="top:524px">
    <svg class="solid" width="6" height="6" viewBox="0 0 12 12"><path d="M2.5 0.5h2l1 3-1.5 1a7 7 0 0 0 3.5 3.5l1-1.5 3 1v2a1 1 0 0 1-1 1A10 10 0 0 1 1.5 1.5a1 1 0 0 1 1-1z"/></svg>
    1 (555) 384-2917</div>
  <div class="abs contact" style="top:534px">
    <svg width="6" height="5" viewBox="0 0 12 9" stroke-width="1.2"><rect x="0.6" y="0.6" width="10.8" height="7.8"/><polyline points="0.6,0.6 6,5 11.4,0.6"/></svg>
    Gareth@harborkey-example.ca</div>
  <div class="dash" style="right:36px;top:528px;width:18px"></div>
  <div class="abs web">www.Harborkey-example.ca</div>
  <div class="bottom-band" style="height:8px"></div>
</section>

<!-- Business card front -->
<section class="piece card-front" aria-label="Business card front">
  <div class="abs wordmark">HARBORKEY</div>
  <div class="abs tagline">PROPERTY MANAGEMENT</div>
  <div class="abs person">Gareth Lindqvist</div>
  <div class="abs role">Operations Manager</div>
  <div class="abs contact" style="top:83px">
    <svg class="solid" width="4" height="4" viewBox="0 0 12 12"><path d="M2.5 0.5h2l1 3-1.5 1a7 7 0 0 0 3.5 3.5l1-1.5 3 1v2a1 1 0 0 1-1 1A10 10 0 0 1 1.5 1.5a1 1 0 0 1 1-1z"/></svg>
    1 (555) 384-2917</div>
  <div class="abs contact" style="top:90px">
    <svg width="4" height="3.5" viewBox="0 0 12 9" stroke-width="1.4"><rect x="0.7" y="0.7" width="10.6" height="7.6"/><polyline points="0.7,0.7 6,5 11.3,0.7"/></svg>
    Gareth@harborkey-example.ca</div>
  <div class="dash" style="right:18px;top:85px;width:13px;height:1.5px"></div>
  <div class="abs web">www.Harborkey-example.ca</div>
  <div class="bottom-band" style="height:3px"></div>
</section>

<!-- Business card back -->
<section class="piece card-back on-green" aria-label="Business card back">
  <div class="abs wordmark">HARBORKEY</div>
  <div class="abs tagline">PROPERTY MANAGEMENT</div>
  <div class="abs web-light">www.Harborkey-example.ca</div>
</section>

<!-- Email signature -->
<section class="piece email-sig" aria-label="Email signature">
  <div class="brand-panel on-green">
    <div class="abs wordmark">HARBORKEY</div>
    <div class="abs tagline">PROPERTY MANAGEMENT</div>
  </div>
  <div class="abs person">Gareth Lindqvist</div>
  <div class="abs role">Operations Manager</div>
  <div class="social" aria-label="Social profiles"><span></span><span></span><span></span><span></span></div>
  <div class="abs contact" style="top:55px">
    <svg class="solid" width="5" height="5" viewBox="0 0 12 12"><path d="M2.5 0.5h2l1 3-1.5 1a7 7 0 0 0 3.5 3.5l1-1.5 3 1v2a1 1 0 0 1-1 1A10 10 0 0 1 1.5 1.5a1 1 0 0 1 1-1z"/></svg>
    1 (555) 384-2917</div>
  <div class="abs contact" style="top:64px">
    <svg width="5" height="4" viewBox="0 0 12 9" stroke-width="1.3"><rect x="0.6" y="0.6" width="10.8" height="7.8"/><polyline points="0.6,0.6 6,5 11.4,0.6"/></svg>
    Gareth@harborkey-example.ca</div>
  <div class="dash" style="right:19px;top:57px;width:16px"></div>
  <div class="abs web">www.Harborkey-example.ca</div>
</section>

<!-- #10 Envelope front -->
<section class="piece envelope-front" aria-label="Envelope front">
  <div class="abs wordmark">HARBORKEY</div>
  <div class="abs tagline">PROPERTY MANAGEMENT</div>
  <div class="abs contact" style="top:154px">
    <svg class="solid" width="6" height="6" viewBox="0 0 12 12"><path d="M2.5 0.5h2l1 3-1.5 1a7 7 0 0 0 3.5 3.5l1-1.5 3 1v2a1 1 0 0 1-1 1A10 10 0 0 1 1.5 1.5a1 1 0 0 1 1-1z"/></svg>
    1 (555) 384-2917</div>
  <div class="abs contact" style="top:164px">
    <svg width="6" height="5" viewBox="0 0 12 9" stroke-width="1.2"><rect x="0.6" y="0.6" width="10.8" height="7.8"/><polyline points="0.6,0.6 6,5 11.4,0.6"/></svg>
    Gareth@harborkey-example.ca</div>
  <div class="dash" style="right:39px;top:157px;width:18px"></div>
  <div class="abs web">www.Harborkey-example.ca</div>
  <div class="bottom-band" style="height:5px"></div>
</section>

<!-- #10 Envelope back -->
<section class="piece envelope-back on-green" aria-label="Envelope back">
  <svg class="shape" width="440" height="192" viewBox="0 0 440 192">
    <rect x="0" y="0" width="440" height="192" fill="#ffffff"/>
    <path d="M7 50 Q4 120 9 192" fill="none" stroke="#d8d8d8" stroke-width="0.8"/>
    <path d="M433 50 Q436 120 431 192" fill="none" stroke="#d8d8d8" stroke-width="0.8"/>
    <path d="M14 54 Q18 66 32 66 H408 Q422 66 426 54" fill="none" stroke="#e6e6e6" stroke-width="2"/>
    <path d="M0 0 H440 L427 51 Q424 63 410 63 H30 Q16 63 13 51 Z" fill="#80a83f"/>
  </svg>
  <div class="abs wordmark">HARBORKEY</div>
  <div class="abs tagline">PROPERTY MANAGEMENT</div>
</section>

</body>
</html>
```